Travel Agency Website - Simple General

Need a 7 page simple design that is pretty repetitive. Need to be able to load quickly that is SEO optimized. Trying to give ideas on what they can do, be personal as we are local, but at the same time come across as professional and get information easily with little burden.

- Landing Page
- Brimwell Vacations Page
- Family Trips
- Road Trips from Texas
- Other Destinations
- About Us Page
- Contact Us Page

Target Market(s)

Families

Coding

Coded - Design and coding required

Number of Pages Required

5+ page

Colors

Designer to choose colors to be used in the design.

Requirements
Must have
• Like it to flow easily with our logo. Use that for colors, etc.

```html
<!DOCTYPE html>
<html lang="en">
<head>
<meta charset="utf-8">
<title>Texas Road Trips Page – Meadowlark Travel</title>
<link href="https://fonts.googleapis.com/css2?family=Outfit:wght@300;400;500;600;700;800&display=swap" rel="stylesheet">
<style>
:root{
  --board:#a3a3a3;
  --teal:#1d5b67;
  --teal-dark:#174a55;
  --ink:#23505a;
  --gold:#c4964a;
  --gold-soft:#d9b57a;
  --cream:#f4f2eb;
  --card:#f7f6f1;
  --mint:#dde9e7;
  --line:#c9d3d2;
  --row-alt:#f4f0e9;
  --white:#ffffff;
}
*{box-sizing:border-box;margin:0;padding:0}
html,body{width:1200px;height:944px;overflow:hidden}
body{background:var(--board);font-family:"Outfit",sans-serif;color:var(--ink);position:relative}
.board-title{position:absolute;top:34px;left:0;width:1200px;text-align:center;color:var(--white);font-weight:700;font-size:61px;letter-spacing:1px;line-height:1}

.page{position:absolute;top:180px;width:502px;background:var(--cream);overflow:hidden}
.page--centered{left:80px;height:606px}
.page--photo{left:618px;height:697px}

.hero-bg{position:absolute;left:0;top:0;width:100%;height:330px;background:linear-gradient(180deg,#e6efee 0%,#dbe8e6 45%,#e9eeea 75%,var(--cream) 100%)}
.page--photo .hero-bg{height:260px;background:linear-gradient(180deg,#f2f1ea 0%,#f4f2ea 100%)}
.form-bg{position:absolute;left:0;bottom:35px;width:100%;height:150px;background:linear-gradient(180deg,var(--cream) 0%,#e3ebe8 60%,#eef1ec 100%)}
.hero-photo{position:absolute;left:244px;top:0;width:258px;height:240px;
  background:
   linear-gradient(90deg,#f4f2ea 0%,rgba(244,242,234,0) 30%),
   linear-gradient(0deg,#f4f2ea 0%,rgba(244,242,234,0) 25%),
   linear-gradient(160deg,#e9e3cf 0%,#c9a56a 30%,#8e8a4c 55%,#5f7a3a 75%,#7d8a5e 100%)}

.contact-bar{position:absolute;left:225px;top:0;width:233px;height:17px;background:var(--teal);border-radius:0 0 5px 5px;display:flex;align-items:center;gap:9px;padding-left:9px;color:var(--white);font-size:5.6px;font-weight:500}
.page--photo .contact-bar{height:18px}
.contact-bar span{display:flex;align-items:center;gap:4px}
.contact-bar svg{width:10px;height:10px}

.brand{position:absolute;left:30px;top:22px;display:flex;align-items:center;gap:5px}
.brand-dot{width:10px;height:10px;border-radius:50%;background:var(--gold)}
.brand-name{font-size:11px;font-weight:600;color:var(--teal);line-height:1.05}

.nav{position:absolute;left:0;top:30px;width:100%;height:10px;font-size:6.2px;font-weight:500;color:var(--ink)}
.page--photo .nav{top:32px}
.nav a{position:absolute;top:0;color:inherit;text-decoration:none;white-space:nowrap}
.nav .active{border-bottom:1px solid var(--gold);padding-bottom:3px}
.nav .home{left:129px;top:0}
.nav .home svg{width:6px;height:6px}
.btn-contact{position:absolute;left:399px;top:-4px;width:58px;height:16px;border-radius:8px;background:var(--gold);color:var(--white);font-size:5.8px;display:flex;align-items:center;padding-left:11px;gap:6px}
.arrow-dot{width:11px;height:11px;border-radius:50%;background:var(--gold-soft);display:flex;align-items:center;justify-content:center}
.arrow-dot svg{width:5px;height:5px}

.hero-copy--centered{position:absolute;top:67px;left:0;width:100%;text-align:center}
.eyebrow{font-size:9px;font-weight:400;color:var(--teal);letter-spacing:.3px}
.hero-title{font-size:20px;font-weight:700;color:var(--teal);letter-spacing:.4px;line-height:1.1;margin-top:3px}
.partner{display:flex;align-items:center;justify-content:center;gap:4px;margin-top:9px;font-size:8px;font-weight:400;color:var(--teal)}
.partner-mark{width:10px;height:10px;border:1px solid var(--gold);border-radius:50%}
.partner-name{font-weight:500;letter-spacing:.3px}

.hero-copy--left{position:absolute;top:94px;left:54px;width:200px}
.hero-copy--left .hero-title{font-size:21.5px;line-height:1.06;margin-top:2px}
.hero-copy--left .partner{justify-content:flex-start;margin-top:8px;font-size:7.4px}
.hero-copy--left .partner-name{font-size:6px;font-weight:600;line-height:1.15}
.hero-copy--left .lead{margin-top:10px;font-size:5.6px;line-height:1.45;color:#4f6c72;width:150px}

.trips{position:absolute;left:48px;width:419px;border:1px solid var(--line);border-radius:3px;overflow:hidden;background:var(--white)}
.trips table{width:100%;border-collapse:collapse;table-layout:fixed}
.trips th{background:var(--teal);color:var(--white);font-size:5.4px;font-weight:500;height:18px;text-align:left}
.trips td{font-size:6px;height:24px;color:var(--ink)}
.trips tr:nth-child(even) td{background:var(--row-alt)}
.trips th:first-child,.trips td:first-child{padding-left:21px}
.page--centered .trips{top:151px}
.page--photo .trips{top:242px}

.plan{position:absolute;left:46px;width:419px;height:253px;background:var(--card);border:1px solid #dedbd0;border-radius:3px}
.page--centered .plan{top:295px}
.page--photo .plan{top:385px}
.plan h2{position:absolute;top:20px;left:0;width:100%;text-align:center;font-size:13px;font-weight:700;color:var(--teal);letter-spacing:.3px}
.plan label,.plan .label{position:absolute;font-size:6.8px;font-weight:500;color:var(--ink)}
.field{position:absolute;height:23px;border:1px solid #9fb3b6;background:var(--white);display:flex;align-items:center;font-size:6.4px;font-weight:300;color:#3d5a60;padding-left:10px;justify-content:space-between;padding-right:10px}
.field svg{width:7px;height:7px}
.field--date{justify-content:flex-start;gap:5px;padding-left:7px}
.field--notes{align-items:flex-start;padding-top:8px;height:46px}
.btn-plan{position:absolute;left:159px;top:212px;width:105px;height:21px;border-radius:11px;background:var(--gold);color:var(--white);font-size:8px;font-weight:600;display:flex;align-items:center;justify-content:center;gap:8px;padding-left:8px}
.btn-plan .arrow-dot{width:13px;height:13px}

.site-footer{position:absolute;left:0;bottom:0;width:100%;height:35px;background:var(--white);font-size:5.2px;color:#333}
.site-footer p{position:absolute;left:0;width:496px;text-align:center;top:14px}
.social{position:absolute;left:419px;top:11px;display:flex;gap:3px}
.social span{width:9px;height:9px;border-radius:50%;background:var(--teal)}
</style>
</head>
<body>
<h1 class="board-title">TEXAS ROAD TRIPS PAGE</h1>

<!-- Centered hero variant -->
<section class="page page--centered">
  <div class="hero-bg" role="img" aria-label="Soft misty mountain range in pale mint tones"></div>

  <div class="contact-bar">
    <span><svg viewBox="0 0 10 10"><circle cx="5" cy="5" r="5" fill="#fff"/><rect x="2.5" y="3.3" width="5" height="3.6" fill="none" stroke="#1d5b67" stroke-width=".7"/><path d="M2.5 3.3L5 5.3 7.5 3.3" fill="none" stroke="#1d5b67" stroke-width=".7"/></svg>hello@meadowlarktravel.com</span>
    <span><svg viewBox="0 0 10 10"><circle cx="5" cy="5" r="5" fill="#fff"/><path d="M3.4 2.6l1 1-.5.8a3.5 3.5 0 0 0 1.7 1.7l.8-.5 1 1-.6.8C5 7.3 2.7 5 2.6 3.2z" fill="#1d5b67"/></svg>Phone Number (555) 014 7290</span>
  </div>

  <div class="brand"><span class="brand-dot"></span><span class="brand-name">Meadowlark<br>Travel</span></div>

  <nav class="nav">
    <a class="home" href="#"><svg viewBox="0 0 10 10"><path d="M5 1L1 5h1.3v4h2.2V6.5h1V9h2.2V5H9z" fill="#c4964a"/></svg></a>
    <a style="left:144px" href="#">Brimwell Vacations</a>
    <a style="left:201px" href="#">Family Trips</a>
    <a style="left:243px" class="active" href="#">Texas Road Trips</a>
    <a style="left:299px" href="#">Other Destinations</a>
    <a style="left:367px" href="#">About Us</a>
    <a class="btn-contact" href="#">Contact Us <span class="arrow-dot"><svg viewBox="0 0 6 6"><path d="M1 5L5 1M2 1h3v3" fill="none" stroke="#fff" stroke-width=".8"/></svg></span></a>
  </nav>

  <div class="hero-copy--centered">
    <p class="eyebrow">TEXAS ROAD TRIPS</p>
    <h2 class="hero-title">ROAD TRIPS FROM TEXAS</h2>
    <p class="partner">In Partnership with <span class="partner-mark"></span><span class="partner-name">PINEY TRAIL VAN RENTAL</span></p>
  </div>

  <div class="trips">
    <table>
      <colgroup><col style="width:77px"><col style="width:53px"><col style="width:50px"><col style="width:66px"><col style="width:59px"><col style="width:52px"><col></colgroup>
      <thead><tr><th>Trip Name</th><th>Duration</th><th>Best For</th><th>Destination</th><th>Price Range</th><th>Difficulty</th><th>Van Rental</th></tr></thead>
      <tbody>
        <tr><td>TRIP A</td><td>3 Days</td><td>Families</td><td>Big Bend</td><td>$125</td><td>Easy</td><td>Yes</td></tr>
        <tr><td>TRIP B</td><td>5 Days</td><td>Couples</td><td>Hill Country</td><td>$250</td><td>Moderate</td><td>Optional</td></tr>
        <tr><td>TRIP C</td><td>7 Days</td><td>Adventures</td><td>National Parks</td><td>$325</td><td>Moderate</td><td>Yes</td></tr>
        <tr><td>TRIP D</td><td>9 Days</td><td>Adventures</td><td>National Parks</td><td>$450</td><td>Moderate</td><td>Yes</td></tr>
      </tbody>
    </table>
  </div>

  <form class="plan">
    <h2>PLAN YOUR TEXAS ROAD TRIP</h2>
    <label style="left:24px;top:55px">What Type of Trip Are You Interested In?</label>
    <label style="left:216px;top:55px">How Many People in Your Party?</label>
    <div class="field" style="left:24px;top:66px;width:185px">Select<svg viewBox="0 0 8 8"><path d="M1 2.5l3 3 3-3" fill="none" stroke="#23505a" stroke-width="1"/></svg></div>
    <div class="field" style="left:216px;top:66px;width:184px">05<svg viewBox="0 0 8 8"><path d="M1 2.5l3 3 3-3" fill="none" stroke="#23505a" stroke-width="1"/></svg></div>
    <label style="left:24px;top:104px">Do You Need a Van Rental</label>
    <label style="left:219px;top:104px">When Would You Like To Go?</label>
    <div class="field" style="left:24px;top:114px;width:185px">Piney Trail Van Rentals – Tyler, TX</div>
    <div class="field field--date" style="left:217px;top:114px;width:89px"><svg viewBox="0 0 8 8"><rect x=".5" y="1.2" width="7" height="6.3" fill="none" stroke="#9aa" stroke-width=".6"/><path d="M.5 3h7" stroke="#9aa" stroke-width=".6"/></svg>Start Date</div>
    <div class="field field--date" style="left:311px;top:114px;width:89px"><svg viewBox="0 0 8 8"><rect x=".5" y="1.2" width="7" height="6.3" fill="none" stroke="#9aa" stroke-width=".6"/><path d="M.5 3h7" stroke="#9aa" stroke-width=".6"/></svg>End Date</div>
    <label style="left:24px;top:148px">Any Additional Notes</label>
    <div class="field field--notes" style="left:24px;top:157px;width:376px">Type here</div>
    <div class="btn-plan">Start Planning <span class="arrow-dot"><svg viewBox="0 0 6 6"><path d="M1 5L5 1M2 1h3v3" fill="none" stroke="#fff" stroke-width=".8"/></svg></span></div>
  </form>

  <footer class="site-footer">
    <p>© 2026 Meadowlark Travel. All Right Reserved</p>
    <div class="social"><span></span><span></span></div>
  </footer>
</section>

<!-- Photo hero variant -->
<section class="page page--photo">
  <div class="hero-bg"></div>
  <div class="form-bg" role="img" aria-label="Faint misty mountain silhouettes"></div>
  <div class="hero-photo" role="img" aria-label="Photo of golden sandstone cliffs above a winding road through green Texas hills"></div>

  <div class="contact-bar">
    <span><svg viewBox="0 0 10 10"><circle cx="5" cy="5" r="5" fill="#fff"/><rect x="2.5" y="3.3" width="5" height="3.6" fill="none" stroke="#1d5b67" stroke-width=".7"/><path d="M2.5 3.3L5 5.3 7.5 3.3" fill="none" stroke="#1d5b67" stroke-width=".7"/></svg>hello@meadowlarktravel.com</span>
    <span><svg viewBox="0 0 10 10"><circle cx="5" cy="5" r="5" fill="#fff"/><path d="M3.4 2.6l1 1-.5.8a3.5 3.5 0 0 0 1.7 1.7l.8-.5 1 1-.6.8C5 7.3 2.7 5 2.6 3.2z" fill="#1d5b67"/></svg>Phone Number (555) 014 7290</span>
  </div>

  <div class="brand"><span class="brand-dot"></span><span class="brand-name">Meadowlark<br>Travel</span></div>

  <nav class="nav">
    <a class="home" href="#"><svg viewBox="0 0 10 10"><path d="M5 1L1 5h1.3v4h2.2V6.5h1V9h2.2V5H9z" fill="#c4964a"/></svg></a>
    <a style="left:144px" href="#">Brimwell Vacations</a>
    <a style="left:201px" href="#">Family Trips</a>
    <a style="left:243px" class="active" href="#">Texas Road Trips</a>
    <a style="left:299px" href="#">Other Destinations</a>
    <a style="left:367px" href="#">About Us</a>
    <a class="btn-contact" href="#">Contact Us <span class="arrow-dot"><svg viewBox="0 0 6 6"><path d="M1 5L5 1M2 1h3v3" fill="none" stroke="#fff" stroke-width=".8"/></svg></span></a>
  </nav>

  <div class="hero-copy--left">
    <p class="eyebrow">TEXAS ROAD TRIPS</p>
    <h2 class="hero-title">ROAD TRIPS<br>FROM TEXAS</h2>
    <p class="partner">In Partnership with <span class="partner-mark"></span><span class="partner-name">PINEY TRAIL<br>VAN RENTAL</span></p>
    <p class="lead">Scenic routes. Unforgettable places. Epic adventures. Explore handpicked road trips perfect for families, couples, and adventure seekers.</p>
  </div>

  <div class="trips">
    <table>
      <colgroup><col style="width:77px"><col style="width:53px"><col style="width:50px"><col style="width:66px"><col style="width:59px"><col style="width:52px"><col></colgroup>
      <thead><tr><th>Trip Name</th><th>Duration</th><th>Best For</th><th>Destination</th><th>Price Range</th><th>Difficulty</th><th>Van Rental</th></tr></thead>
      <tbody>
        <tr><td>TRIP A</td><td>3 Days</td><td>Families</td><td>Big Bend</td><td>$125</td><td>Easy</td><td>Yes</td></tr>
        <tr><td>TRIP B</td><td>5 Days</td><td>Couples</td><td>Hill Country</td><td>$250</td><td>Moderate</td><td>Optional</td></tr>
        <tr><td>TRIP C</td><td>7 Days</td><td>Adventures</td><td>National Parks</td><td>$325</td><td>Moderate</td><td>Yes</td></tr>
        <tr><td>TRIP D</td><td>9 Days</td><td>Adventures</td><td>National Parks</td><td>$450</td><td>Moderate</td><td>Yes</td></tr>
      </tbody>
    </table>
  </div>

  <form class="plan">
    <h2>PLAN YOUR TEXAS ROAD TRIP</h2>
    <label style="left:24px;top:55px">What Type of Trip Are You Interested In?</label>
    <label style="left:216px;top:55px">How Many People in Your Party?</label>
    <div class="field" style="left:24px;top:66px;width:185px">Select<svg viewBox="0 0 8 8"><path d="M1 2.5l3 3 3-3" fill="none" stroke="#23505a" stroke-width="1"/></svg></div>
    <div class="field" style="left:216px;top:66px;width:184px">05<svg viewBox="0 0 8 8"><path d="M1 2.5l3 3 3-3" fill="none" stroke="#23505a" stroke-width="1"/></svg></div>
    <label style="left:24px;top:104px">Do You Need a Van Rental</label>
    <label style="left:219px;top:104px">When Would You Like To Go?</label>
    <div class="field" style="left:24px;top:114px;width:185px">Piney Trail Van Rentals – Tyler, TX</div>
    <div class="field field--date" style="left:217px;top:114px;width:89px"><svg viewBox="0 0 8 8"><rect x=".5" y="1.2" width="7" height="6.3" fill="none" stroke="#9aa" stroke-width=".6"/><path d="M.5 3h7" stroke="#9aa" stroke-width=".6"/></svg>Start Date</div>
    <div class="field field--date" style="left:311px;top:114px;width:89px"><svg viewBox="0 0 8 8"><rect x=".5" y="1.2" width="7" height="6.3" fill="none" stroke="#9aa" stroke-width=".6"/><path d="M.5 3h7" stroke="#9aa" stroke-width=".6"/></svg>End Date</div>
    <label style="left:24px;top:148px">Any Additional Notes</label>
    <div class="field field--notes" style="left:24px;top:157px;width:376px">Type here</div>
    <div class="btn-plan">Start Planning <span class="arrow-dot"><svg viewBox="0 0 6 6"><path d="M1 5L5 1M2 1h3v3" fill="none" stroke="#fff" stroke-width=".8"/></svg></span></div>
  </form>

  <footer class="site-footer">
    <p>© 2026 Meadowlark Travel. All Right Reserved</p>
    <div class="social"><span></span><span></span></div>
  </footer>
</section>
</body>
</html>
```